Consulting Company PowerPoint Template Design

We are looking for an updated PowerPoint template design or our 55 person energy consulting firm (K7) based in San Francisco (www.kseven-example.com). We would like two versions of the same PowerPoint template in a 16:9 and 4:3 format with our existing logo.

We have an existing color scheme and template and are seeking your help to polish/update the template design for wide format and create a flexible template that is easy to use with content from Excel and Word. Our current template, and a couple of examples that we like are attached.

Specific requests include:

• Dark background for slide title
• A narrow section header
• Maximizing white space for content
• A limited number of well designed Master template layouts to choose from
• A selection of title and section header slides that are not San Francisco specific with some variety to chose from ideally with a focus on energy or nature, graphics/visuals.

For examples of energy specific templates see:
https://www.brightslidehub.example/energy/powerpoint-templates/0.html

Requirements
Must have
• Must use our logo but open to other designs, fonts, and styles for the PowerPoint template.
• Please use our existing color scheme found in the attached Excel file.
• Also we would like the ability to easily copy and paste from our existing/original template to the new template. In other words we would like backward compatibility to apply the new template format to our old PowerPoints that use our existing template.

```html
<!DOCTYPE html>
<html lang="en">
<head>
<meta charset="utf-8">
<title>Our Organise Chart</title>
<link href="https://fonts.googleapis.com/css2?family=Cabin:wght@500;600;700&family=Lato:wght@400;700&display=swap" rel="stylesheet">
<style>
  :root {
    --navy: #0d4a6b;
    --gold: #d6b25e;
    --gold-light: #e7cd8d;
    --ink: #333333;
    --line: #c9c9c9;
    --green: #7ab648;
    --blue: #3a8fd9;
    --slate: #475466;
    --orange: #f29a2e;
    --red: #e8253f;
    --grey: #a3a3a3;
    --bg: #ffffff;
  }
  * { margin: 0; padding: 0; box-sizing: border-box; }
  html, body { width: 1200px; height: 900px; overflow: hidden; background: var(--bg); }
  .slide { position: relative; width: 1200px; height: 900px; font-family: "Lato", sans-serif; color: var(--ink); }
  .title-accent { position: absolute; left: 0; top: 21px; width: 12px; height: 66px; background: var(--gold); }
  .slide-title { position: absolute; left: 27px; top: 24px; font-family: "Cabin", sans-serif; font-weight: 600; font-size: 40px; color: var(--navy); letter-spacing: 0.2px; }
  .brand { position: absolute; right: 22px; top: 22px; display: flex; align-items: center; gap: 10px; }
  .brand-dot { width: 18px; height: 18px; border-radius: 50%; background: var(--gold); }
  .brand-name { font-family: "Cabin", sans-serif; font-weight: 700; font-size: 38px; color: var(--navy); }
  .intro { position: absolute; left: 63px; top: 155px; width: 1070px; font-size: 19px; line-height: 32.5px; color: var(--ink); }
  .timeline { position: absolute; left: 0; top: 0; }
  .year { font-family: "Lato", sans-serif; font-weight: 700; font-size: 22px; fill: #fff; text-anchor: middle; }
  .milestone-text { position: absolute; width: 200px; font-size: 17px; line-height: 27px; color: var(--ink); }
  .milestone-text.below { text-align: right; }
  .footer { position: absolute; left: 0; bottom: 0; width: 1200px; height: 45px; background: var(--navy); }
  .footer-name { position: absolute; left: 12px; top: 9px; font-family: "Cabin", sans-serif; font-weight: 700; font-size: 21px; color: #fff; }
  .page-tab { position: absolute; right: 0; bottom: 0; }
  .page-number { position: absolute; right: 20px; bottom: 6px; font-family: "Cabin", sans-serif; font-weight: 600; font-size: 28px; color: #fff; }
</style>
</head>
<body>
<main class="slide">
  <div class="title-accent"></div>
  <h1 class="slide-title">Our Organise Chart</h1>
  <div class="brand"><span class="brand-dot"></span><span class="brand-name">K7</span></div>

  <p class="intro">Lorem ipsum dolor sit Lorem ipsum dolor sit&nbsp; Lorem ipsum dolor sit Lorem ipsum dolor sit&nbsp; Lorem ipsum dolor sit Lorem ipsum dolor sit&nbsp; Lorem ipsum dolor sit Lorem ipsum dolor sit&nbsp; Lorem ipsum dolor sit Lorem ipsum dolor sit&nbsp; Lorem ipsum dolor sit Lorem ipsum dolor sit&nbsp; Lorem ipsum dolor sit Lorem ipsum dolor sit</p>

  <svg class="timeline" width="1200" height="900" viewBox="0 0 1200 900" aria-hidden="true">
    <g class="connectors" stroke="var(--line)" stroke-width="1.5">
      <line x1="121" y1="468" x2="121" y2="520"/>
      <line x1="497" y1="468" x2="497" y2="520"/>
      <line x1="876" y1="468" x2="876" y2="520"/>
      <line x1="303" y1="591" x2="303" y2="645"/>
      <line x1="681" y1="591" x2="681" y2="645"/>
      <line x1="1060" y1="591" x2="1060" y2="645"/>
    </g>

    <g class="band">
      <polygon fill="var(--green)"  points="21,534 210,534 228,555 210,576 21,576 39,555"/>
      <polygon fill="var(--blue)"   points="210,534 399,534 417,555 399,576 210,576 228,555"/>
      <polygon fill="var(--slate)"  points="399,534 588,534 606,555 588,576 399,576 417,555"/>
      <polygon fill="var(--orange)" points="588,534 777,534 795,555 777,576 588,576 606,555"/>
      <polygon fill="var(--red)"    points="777,534 966,534 984,555 966,576 777,576 795,555"/>
      <polygon fill="var(--grey)"   points="966,534 1155,534 1173,555 1155,576 966,576 984,555"/>
      <text class="year" x="123" y="563">1986</text>
      <text class="year" x="312" y="563">1990</text>
      <text class="year" x="501" y="563">2000</text>
      <text class="year" x="690" y="563">2005</text>
      <text class="year" x="879" y="563">2011</text>
      <text class="year" x="1069" y="563">2015</text>
    </g>

    <g class="badges" fill="#fff" stroke-width="1.5">
      <circle cx="121" cy="380" r="63" stroke="var(--green)"/>
      <circle cx="497" cy="380" r="63" stroke="var(--slate)"/>
      <circle cx="876" cy="380" r="63" stroke="var(--red)"/>
      <circle cx="303" cy="723" r="63" stroke="var(--blue)"/>
      <circle cx="681" cy="723" r="63" stroke="var(--orange)"/>
      <circle cx="1060" cy="723" r="63" stroke="var(--grey)"/>
    </g>

    <g class="icon-cubes" fill="none" stroke="var(--green)" stroke-width="3" stroke-linejoin="round">
      <rect x="104" y="347" width="28" height="28"/>
      <rect x="88" y="375" width="28" height="28"/>
      <rect x="120" y="375" width="28" height="28"/>
      <path d="M104 347l6-6h28l-6 6M132 375l6-6v-22"/>
      <path d="M88 375l6-6h10M148 375l6-6v28l-6 6"/>
    </g>

    <g class="icon-database" fill="none" stroke="var(--slate)" stroke-width="3">
      <ellipse cx="487" cy="362" rx="17" ry="6"/>
      <path d="M470 362v36c0 4 8 6 17 6s17-2 17-6v-36M470 374c0 4 8 6 17 6s17-2 17-6M470 386c0 4 8 6 17 6s17-2 17-6"/>
      <ellipse cx="510" cy="356" rx="15" ry="5"/>
      <path d="M504 360c8 0 21-1 21-4v30c0 3-8 5-21 5M504 372c10 0 21-1 21-4"/>
    </g>

    <g class="icon-gears" fill="none" stroke="var(--red)" stroke-width="3">
      <circle cx="864" cy="393" r="11"/>
      <circle cx="864" cy="393" r="4"/>
      <path d="M864 378v-5M864 408v5M849 393h-5M879 393h5M853 382l-4-4M875 404l4 4M853 404l-4 4M875 382l4-4"/>
      <circle cx="891" cy="366" r="8"/>
      <circle cx="891" cy="366" r="3"/>
      <path d="M891 355v-4M891 377v4M880 366h-4M902 366h4M883 358l-3-3M899 374l3 3M883 374l-3 3M899 358l3-3"/>
    </g>

    <g class="icon-pencil" fill="none" stroke="var(--blue)" stroke-width="3" stroke-linejoin="round">
      <path d="M283 747l6-20 34-34 14 14-34 34z"/>
      <path d="M289 727l14 14M317 699l14 14"/>
    </g>

    <g class="icon-briefcase" fill="none" stroke="var(--orange)" stroke-width="3" stroke-linejoin="round">
      <rect x="648" y="703" width="66" height="44" rx="4"/>
      <path d="M670 703v-8h22v8M648 722h66"/>
      <rect x="676" y="717" width="10" height="10"/>
    </g>

    <g class="icon-award" fill="none" stroke="var(--grey)" stroke-width="3" stroke-linejoin="round">
      <path d="M1060 691l6 5 8-1 2 7 7 4-3 7 3 7-7 4-2 7-8-1-6 5-6-5-8 1-2-7-7-4 3-7-3-7 7-4 2-7 8 1z"/>
      <circle cx="1060" cy="713" r="12"/>
      <path d="M1048 734l-8 20 8-3 4 7 6-17M1072 734l8 20-8-3-4 7-6-17"/>
    </g>

    <g class="page-tab-shape">
      <polygon fill="var(--gold-light)" points="1107,855 1200,855 1200,900 1122,900"/>
      <polygon fill="var(--gold)" points="1116,858 1200,858 1200,900 1130,900"/>
    </g>
  </svg>

  <p class="milestone-text" style="left:210px; top:322px;">Lorem Ipsum is<br>simply dummy text of<br>the printing and<br>typesetting industry.</p>
  <p class="milestone-text" style="left:584px; top:329px;">Lorem Ipsum is<br>simply dummy text of<br>the printing and<br>typesetting industry.</p>
  <p class="milestone-text" style="left:972px; top:331px;">Lorem Ipsum is<br>simply dummy text of<br>the printing and<br>typesetting industry.</p>

  <p class="milestone-text below" style="left:19px; top:664px;">Lorem Ipsum is<br>simply dummy text of<br>the printing and<br>typesetting industry.</p>
  <p class="milestone-text below" style="left:387px; top:670px;">Lorem Ipsum is<br>simply dummy text of<br>the printing and<br>typesetting industry.</p>
  <p class="milestone-text below" style="left:765px; top:672px;">Lorem Ipsum is<br>simply dummy text of<br>the printing and<br>typesetting industry.</p>

  <footer class="footer">
    <span class="footer-name">Kinetic Seven Economics</span>
  </footer>
  <span class="page-number">1</span>
</main>
</body>
</html>
```